Copper lark buildworks

Copper lark buildworks is a small construction company.
Who is a licenced builder, Carpenter, joiner,
working on heritage ,new build, speacial projects and sometimes furniture

Industry/Entity Type

Construction

```html
<!DOCTYPE html>
<html lang="en">
<head>
<meta charset="utf-8">
<title>Copper lark buildworks – business cards</title>
<link rel="stylesheet" href="https://fonts.googleapis.com/css2?family=Open+Sans:wght@400;600&display=swap">
<style>
  :root {
    --brand-green: #8cc63f;
    --ink: #111111;
    --paper: #ffffff;
    --backdrop: #e9e6e1;
    --muted: #2a2a2a;
  }
  html, body {
    margin: 0;
    padding: 0;
    width: 1200px;
    height: 880px;
    overflow: hidden;
    background: var(--backdrop);
    font-family: "Open Sans", Arial, sans-serif;
  }
  .canvas {
    position: relative;
    width: 1200px;
    height: 880px;
  }
  .card {
    position: absolute;
    width: 620px;
    height: 354px;
    border-radius: 22px;
    overflow: hidden;
    box-shadow: 0 12px 30px rgba(0,0,0,0.28);
  }
  /* Front */
  .card-front {
    left: 80px;
    top: 50px;
    background: var(--brand-green);
  }
  .front-brand {
    position: absolute;
    left: 0;
    right: 0;
    top: 130px;
    display: flex;
    justify-content: center;
    align-items: center;
    gap: 14px;
  }
  .brand-dot {
    width: 26px;
    height: 26px;
    border-radius: 50%;
    background: var(--ink);
  }
  .brand-name {
    font-weight: 600;
    font-size: 36px;
    letter-spacing: -0.5px;
    color: var(--ink);
  }
  .front-web {
    position: absolute;
    left: 0;
    right: 0;
    top: 212px;
    text-align: center;
    color: var(--paper);
    font-size: 14px;
    letter-spacing: 4px;
  }
  /* Back */
  .card-back {
    left: 500px;
    top: 470px;
    background: var(--paper);
  }
  .back-waves {
    position: absolute;
    inset: 0;
  }
  .back-brand {
    position: absolute;
    left: 40px;
    top: 118px;
    display: flex;
    align-items: center;
    gap: 12px;
  }
  .back-brand .brand-dot {
    background: var(--brand-green);
    width: 22px;
    height: 22px;
  }
  .back-brand .brand-name {
    font-size: 30px;
    color: var(--brand-green);
  }
  .holder {
    position: absolute;
    right: 30px;
    top: 28px;
    text-align: right;
  }
  .holder-name {
    font-size: 21px;
    color: var(--ink);
    line-height: 1.1;
  }
  .holder-name .surname { color: var(--brand-green); }
  .holder-role {
    font-size: 13px;
    color: var(--muted);
  }
  .contacts {
    position: absolute;
    right: 22px;
    top: 222px;
    list-style: none;
    margin: 0;
    padding: 0;
    color: var(--paper);
    font-size: 14px;
  }
  .contacts li {
    display: flex;
    justify-content: flex-end;
    align-items: center;
    gap: 10px;
    height: 24px;
  }
  .contact-icon {
    width: 18px;
    height: 18px;
  }
</style>
</head>
<body>
<main class="canvas">

  <section class="card card-front" aria-label="Card front">
    <div class="front-brand">
      <span class="brand-dot"></span>
      <span class="brand-name">Copper lark buildworks</span>
    </div>
    <div class="front-web">www.copperlarkbuild.com</div>
  </section>

  <section class="card card-back" aria-label="Card back">
    <svg class="back-waves" viewBox="0 0 620 354" width="620" height="354" aria-hidden="true">
      <path d="M0 316 C150 322 255 300 305 214 C285 292 180 336 0 338 Z" fill="var(--brand-green)"/>
      <path d="M620 96 C470 96 410 206 352 288 C312 334 240 340 0 340 L0 354 L620 354 Z" fill="var(--ink)"/>
      <path d="M610 112 C478 122 422 222 364 298 C332 332 292 344 250 348" fill="none" stroke="var(--paper)" stroke-width="5"/>
    </svg>

    <div class="back-brand">
      <span class="brand-dot"></span>
      <span class="brand-name">Copper lark buildworks</span>
    </div>

    <div class="holder">
      <div class="holder-name">Marcus <span class="surname">Hale</span></div>
      <div class="holder-role">President</div>
    </div>

    <ul class="contacts">
      <li>0400 555 217
        <svg class="contact-icon" viewBox="0 0 18 18" aria-hidden="true">
          <circle cx="9" cy="9" r="8" fill="none" stroke="var(--brand-green)" stroke-width="1.5"/>
          <rect x="6" y="4" width="6" height="10" rx="1" fill="none" stroke="var(--brand-green)" stroke-width="1.3"/>
        </svg>
      </li>
      <li>info@copperlarkmail.com
        <svg class="contact-icon" viewBox="0 0 18 18" aria-hidden="true">
          <circle cx="9" cy="9" r="8" fill="var(--brand-green)"/>
          <rect x="4.5" y="6" width="9" height="6.5" fill="none" stroke="var(--ink)" stroke-width="1.2"/>
          <path d="M4.5 6 L9 9.8 L13.5 6" fill="none" stroke="var(--ink)" stroke-width="1.2"/>
        </svg>
      </li>
      <li>www.copperlarkweb.com
        <svg class="contact-icon" viewBox="0 0 18 18" aria-hidden="true">
          <circle cx="9" cy="9" r="8" fill="var(--brand-green)"/>
          <circle cx="9" cy="9" r="4.5" fill="none" stroke="var(--ink)" stroke-width="1.1"/>
          <path d="M4.5 9 H13.5 M9 4.5 V13.5" stroke="var(--ink)" stroke-width="1"/>
        </svg>
      </li>
    </ul>
  </section>

</main>
</body>
</html>
```